A specialised Sport management needs a corporate brochure design

We are a specialized company in the management and consultancy of sports events. and need to have a company brochure
We provide the following services;
Event management
Venues management
Production
Ticketing
Consulting
Hospitality
Activity management
Event timing
Branding of event
Event supplies
We need a corporate profile design for our company to showcase the major events that we have covered , with images, information, statistics, surveys, products and services used. We want to highlight our professionalism and execution of the events, experience of the participants, spectators . How we have grown in the past few years and reached the international standards.
Objectives of the work:
To get sponsors and partners for future business and to present Tri-Crest
as not just a sports management company but also a professional sports
events management company.
You can check our website
www.tri-crest.example
Target Market(s)
Sponsors and corporate partners
Industry/Entity Type
Events
Requirements
Must have
- Must Have:
- - Very professional look
- -Some event images,Event information, statistics, surveys, products and services used. We want to highlight our professionalism and execution of the events (Attached)
Nice to have
- Similar momentom of the below design
- http://www.lumavent.example/wp-content/themes/lumavent/pdf/CP-2014-15-V10-Web.pdf

```html
<!DOCTYPE html>
<html lang="en">
<head>
<meta charset="utf-8">
<title>Tri-Crest Sport Management – Brochure Covers</title>
<link rel="stylesheet" href="https://fonts.googleapis.com/css2?family=Russo+One&family=Arimo:wght@400;700&display=swap">
<style>
  :root {
    --bg: #e4e4e4;
    --paper: #ffffff;
    --paper-warm: #f6f5f2;
    --orange: #e8562a;
    --red: #e2301f;
    --red-dark: #c8231a;
    --green: #0e7a40;
    --grey: #7c7c7c;
    --grey-dark: #4a4a4a;
    --ink: #2b2b2b;
  }
  * { box-sizing: border-box; margin: 0; padding: 0; }
  html, body { width: 1200px; height: 799px; overflow: hidden; }
  body { background: var(--bg); font-family: "Arimo", Arial, sans-serif; position: relative; }

  .cover { position: absolute; width: 560px; height: 396px; overflow: hidden; box-shadow: 0 6px 18px rgba(0,0,0,.18); }
  .cover--back { left: 24px; top: 202px; background: var(--paper-warm); }
  .cover--front { left: 616px; top: 202px; background: var(--paper); }

  /* brand mark */
  .brand { display: flex; align-items: center; gap: 8px; }
  .brand__dot { width: 16px; height: 16px; border-radius: 50%; background: var(--orange); }
  .brand__name { font-family: "Arimo", Arial, sans-serif; font-weight: 700; font-size: 20px; color: var(--grey-dark); }

  /* back cover */
  .back__brand { position: absolute; top: 62px; left: 0; right: 0; justify-content: center; }
  .back__tagline { position: absolute; top: 92px; left: 0; right: 0; text-align: center; font-size: 8px; letter-spacing: 2px; color: var(--grey); }
  .contact { position: absolute; top: 140px; left: 0; right: 0; text-align: center; }
  .contact__title { font-weight: 700; font-size: 22px; color: var(--grey); margin-bottom: 16px; }
  .contact__line { font-size: 11px; color: var(--grey); line-height: 17px; }
  .contact__label { color: var(--red); font-weight: 700; }
  .back__band { position: absolute; left: 0; bottom: 0; width: 560px; height: 90px; }

  /* front cover */
  .photo { position: absolute; }
  .photo--event { left: 48px; top: 0; width: 196px; height: 278px; background: linear-gradient(180deg, #c55a32 0%, #a8401f 45%, #3a2018 75%, #5b3a30 100%); }
  .photo--crowd { left: 250px; top: 150px; width: 310px; height: 246px; background: linear-gradient(120deg, #b9a596 0%, #d9c2ad 40%, #efe4da 75%, #f7f1ea 100%); }
  .front__shapes { position: absolute; left: 0; top: 0; width: 560px; height: 396px; }
  .headline { position: absolute; left: 60px; top: 292px; transform: rotate(-9deg); transform-origin: left top; font-family: "Russo One", Arial, sans-serif; font-size: 25px; line-height: 26px; text-transform: uppercase; }
  .headline__top { color: var(--ink); }
  .headline__bottom { color: var(--grey); }
  .front__logo { position: absolute; left: 396px; top: 32px; width: 118px; height: 118px; border-radius: 50%; background: var(--paper); display: flex; align-items: center; justify-content: center; box-shadow: 0 0 0 1px #eee; }
  .front__logo .brand__name { font-size: 16px; }
  .front__logo .brand__dot { width: 12px; height: 12px; }
  .pointer { position: absolute; left: 322px; top: 82px; }
</style>
</head>
<body>

  <section class="cover cover--back" aria-label="Back cover">
    <div class="brand back__brand">
      <span class="brand__dot"></span>
      <span class="brand__name">Tri-Crest</span>
    </div>
    <p class="back__tagline">SPORT MANAGEMENT</p>
    <div class="contact">
      <h2 class="contact__title">Contact Us</h2>
      <p class="contact__line"><span class="contact__label">Mob:</span> 555 0142 318</p>
      <p class="contact__line"><span class="contact__label">Tel:</span> 555 0176 204</p>
      <p class="contact__line"><span class="contact__label">Email:</span> info@tri-crest.example</p>
      <p class="contact__line"><span class="contact__label">Web:</span> www.tri-crest.example</p>
    </div>
    <svg class="back__band" viewBox="0 0 560 90" aria-hidden="true">
      <polygon points="0,40 180,28 560,56 560,90 0,90" fill="#f28a6a"/>
      <polygon points="0,52 200,40 560,68 560,90 0,90" fill="var(--red)"/>
      <polygon points="0,74 560,80 560,90 0,90" fill="var(--red-dark)"/>
    </svg>
  </section>

  <section class="cover cover--front" aria-label="Front cover">
    <div class="photo photo--event" role="img" aria-label="Photo of athletes running into the water at sunset during a sports event"></div>
    <div class="photo photo--crowd" role="img" aria-label="Photo of cheering spectators in a stadium crowd"></div>
    <svg class="front__shapes" viewBox="0 0 560 396" aria-hidden="true">
      <rect x="244" y="0" width="18" height="210" fill="var(--orange)"/>
      <path d="M0,130 Q30,100 70,95 L70,130 Q30,140 0,180 Z" fill="var(--orange)"/>
      <path d="M0,180 Q30,140 70,130 L70,170 Q40,180 20,210 L0,240 Z" fill="#cfcfcf"/>
      <path d="M260,396 A130,130 0 0 1 340,275 L350,300 A100,100 0 0 0 292,396 Z" fill="var(--green)"/>
      <polygon points="0,300 560,215 560,250 0,396" fill="var(--paper)" opacity="0"/>
      <path d="M0,278 L250,278 L250,250 Q270,240 300,238 L250,300 L0,340 Z" fill="var(--paper)"/>
    </svg>
    <h1 class="headline">
      <span class="headline__top">Let’s take care of</span><br>
      <span class="headline__bottom">your next sports event!</span>
    </h1>
    <svg class="pointer" width="66" height="22" viewBox="0 0 66 22" aria-hidden="true">
      <rect x="0" y="2" width="5" height="18" fill="var(--grey)"/>
      <rect x="10" y="2" width="5" height="18" fill="var(--grey)"/>
      <rect x="20" y="2" width="5" height="18" fill="var(--grey)"/>
      <polygon points="32,2 50,11 32,20" fill="var(--grey)"/>
    </svg>
    <div class="front__logo">
      <div class="brand">
        <span class="brand__dot"></span>
        <span class="brand__name">Tri-Crest</span>
      </div>
    </div>
  </section>

</body>
</html>
```